Indy Film Production Company/Studio

We need a business card designed from an existing logo. We are a digital studio/production company that caters to creating genre entertainment, like Action, Horror, and martial arts. The card along with the logo will be used to Brand the company from letter heads to banners. The design will also be used for postcards and Brochures. It should be professional and masculine.
Updates

Thank you to all the designers who have participated. I'm narrowing down who it will be. Thank you again.

Target Market(s)

Investors, Networks, Producers, and actors

Industry/Entity Type

Film Production

Contact Information for Business Card

Teodoro Valbuena
Producer/Writer/Director
www.kestrelpicturehouse.example

Requirements
Must have
• Website address, Facebook icon and Twitter icon possibly in the back of the card.
Nice to have
• Logline of Company: Follow The Action.

```html
<!DOCTYPE html>
<html lang="en">
<head>
<meta charset="utf-8">
<title>Kestrel Picture House – Business Card</title>
<link rel="stylesheet" href="https://fonts.googleapis.com/css2?family=Montserrat:wght@400;600;800&display=swap">
<style>
  :root {
    --bg: #2b2b2d;
    --card-white: #ffffff;
    --brand-red: #e8222d;
    --ink: #2a2a2a;
    --on-red: #ffffff;
  }
  * { box-sizing: border-box; margin: 0; padding: 0; }
  html, body { width: 1200px; height: 900px; overflow: hidden; }
  body {
    background: var(--bg);
    font-family: "Montserrat", Arial, sans-serif;
    position: relative;
  }
  .card {
    position: absolute;
    width: 700px;
    height: 400px;
    background: var(--card-white);
    box-shadow: 0 10px 30px rgba(0,0,0,.45);
    overflow: hidden;
  }
  .card--front { left: 140px; top: 45px; }
  .card--back  { left: 360px; top: 475px; }

  .wordmark {
    display: flex;
    align-items: center;
    gap: 14px;
    color: var(--brand-red);
    font-weight: 800;
    text-transform: uppercase;
    line-height: 1;
  }
  .wordmark__square {
    width: 34px; height: 34px;
    background: var(--brand-red);
    flex: none;
  }
  .wordmark__name { font-size: 34px; letter-spacing: .5px; }

  .card--front .wordmark {
    position: absolute;
    left: 0; right: 0; top: 170px;
    justify-content: center;
  }
  .front-footer {
    position: absolute;
    left: 34px; right: 34px; bottom: 28px;
    display: flex;
    align-items: center;
    justify-content: space-between;
  }
  .social-links { display: flex; gap: 10px; list-style: none; }
  .social-links li {
    width: 24px; height: 24px;
    border-radius: 50%;
    background: var(--brand-red);
  }
  .front-url {
    font-size: 18px;
    color: var(--ink);
  }
  .front-url span { color: var(--brand-red); }

  .back-logo {
    position: absolute;
    left: 0; top: 0;
    width: 330px; height: 400px;
    display: flex;
    align-items: center;
    justify-content: center;
  }
  .back-logo .wordmark { flex-direction: column; gap: 12px; text-align: center; }
  .back-logo .wordmark__name { font-size: 28px; }

  .contact-panel {
    position: absolute;
    left: 330px; top: 0;
    width: 370px; height: 400px;
    background: var(--brand-red);
    color: var(--on-red);
    padding: 118px 28px 0 40px;
  }
  .contact-panel::before {
    content: "";
    position: absolute;
    left: -1px; top: 128px;
    border-left: 16px solid var(--card-white);
    border-top: 14px solid transparent;
    border-bottom: 14px solid transparent;
  }
  .contact-panel__name {
    font-size: 23px;
    font-weight: 600;
    letter-spacing: 1px;
    text-transform: uppercase;
    white-space: nowrap;
  }
  .contact-panel__role {
    font-size: 13px;
    letter-spacing: 1.2px;
    text-transform: uppercase;
    margin: 6px 0 24px 18px;
  }
  .contact-list { list-style: none; margin-left: 18px; }
  .contact-list li {
    display: flex;
    align-items: center;
    gap: 12px;
    font-size: 15px;
    margin-bottom: 9px;
    white-space: nowrap;
  }
  .contact-list svg { width: 15px; height: 15px; flex: none; }
</style>
</head>
<body>

  <section class="card card--front" aria-label="Business card front">
    <div class="wordmark">
      <span class="wordmark__square"></span>
      <span class="wordmark__name">Kestrel Picture House</span>
    </div>
    <div class="front-footer">
      <ul class="social-links">
        <li role="img" aria-label="Social profile link"></li>
        <li role="img" aria-label="Social profile link"></li>
      </ul>
      <p class="front-url">www.<span>kestrelpicturehouse</span>.example</p>
    </div>
  </section>

  <section class="card card--back" aria-label="Business card back">
    <div class="back-logo">
      <div class="wordmark">
        <span class="wordmark__square"></span>
        <span class="wordmark__name">Kestrel<br>Picture House</span>
      </div>
    </div>
    <div class="contact-panel">
      <h1 class="contact-panel__name">Teodoro Valbuena</h1>
      <p class="contact-panel__role">Producer / Writer / Director</p>
      <ul class="contact-list">
        <li>
          <svg viewBox="0 0 24 24" fill="#fff" aria-hidden="true"><path d="M6.6 10.8a15.1 15.1 0 0 0 6.6 6.6l2.2-2.2c.3-.3.7-.4 1-.2 1.1.4 2.3.6 3.6.6.6 0 1 .4 1 1V20c0 .6-.4 1-1 1A17 17 0 0 1 3 4c0-.6.4-1 1-1h3.5c.6 0 1 .4 1 1 0 1.3.2 2.5.6 3.6.1.3 0 .7-.2 1z"/></svg>
          +330 555-0147
        </li>
        <li>
          <svg viewBox="0 0 24 24" fill="none" stroke="#fff" stroke-width="2" aria-hidden="true"><rect x="3" y="5" width="18" height="14" rx="1"/><path d="M3 6l9 7 9-7"/></svg>
          info@kestrelpicturehouse.example
        </li>
        <li>
          <svg viewBox="0 0 24 24" fill="none" stroke="#fff" stroke-width="2" aria-hidden="true"><circle cx="12" cy="12" r="9"/><path d="M3 12h18M12 3c3 3.5 3 14.5 0 18M12 3c-3 3.5-3 14.5 0 18"/></svg>
          www.kestrelpicturehouse.example
        </li>
      </ul>
    </div>
  </section>

</body>
</html>
```